Heritage Hollow Business Cards

Require a business card design. <br/><br/>Needs to include logo (either round or long version) plus these details:<br/>Maya Torvell<br/>Heritage Hollow<br/>maya@kelvadtrading.com.au<br/>02 6481 7395<br/>PO Box Glenwarra NSW 2791<br/>www.heritagehollow.com.au<br/><br/>I need in an editable format so that I can create for multiple staff members. <br/><br/>

Target Market(s)

We are an online store selling renovation products to home owners are builders. Looking for a classic classy design.

Industry/Entity Type

Home And Garden

Contact Information for Business Card

Maya Torvell
Heritage Hollow
maya@kelvadtrading.com.au
02 6481 7395
PO Box Glenwarra NSW 2791
www.heritagehollow.com.au

Colors

Designer to choose colors to be used in the design.

Requirements
Must have
• Must include Logo.

```html
<!DOCTYPE html>
<html lang="en">
<head>
<meta charset="utf-8">
<title>Heritage Hollow Business Cards</title>
<link rel="stylesheet" href="https://fonts.googleapis.com/css2?family=Arimo:wght@400;700&display=swap">
<style>
  :root {
    --backdrop: #e6e6e4;
    --card-dark: #2a2627;
    --card-light: #ffffff;
    --ink: #161616;
    --ink-soft: #e4e4e4;
    --rule: #c9c9c9;
  }
  * { box-sizing: border-box; margin: 0; padding: 0; }
  html, body {
    width: 1200px; height: 1200px; overflow: hidden;
    background: var(--backdrop);
    font-family: "Arimo", Arial, sans-serif;
  }
  .canvas {
    width: 1200px; height: 1200px;
    display: flex; flex-direction: column; align-items: center; justify-content: center;
    gap: 50px;
  }
  .card {
    width: 720px; height: 410px;
    border-radius: 110px 10px 110px 10px;
    box-shadow: 0 10px 30px rgba(0,0,0,.18);
    position: relative;
  }
  .card--front {
    background: var(--card-dark);
    display: flex; align-items: center; justify-content: center; gap: 22px;
  }
  .brand-mark {
    width: 58px; height: 58px; border-radius: 50%;
    border: 2px solid var(--ink-soft);
  }
  .brand-name--front {
    color: var(--ink-soft); font-size: 50px; font-weight: 400; letter-spacing: .5px;
  }
  .card--back {
    background: var(--card-light);
    display: grid; grid-template-columns: 270px 1px 1fr;
    align-items: center;
  }
  .back-brand {
    display: flex; align-items: center; justify-content: center; gap: 14px;
  }
  .brand-mark--small { width: 40px; height: 40px; border-color: var(--ink); }
  .brand-name--back {
    color: var(--ink); font-size: 30px; line-height: 1.05; font-weight: 400;
  }
  .divider { width: 1px; height: 250px; background: var(--rule); }
  .details { padding-left: 34px; color: var(--ink); }
  .person-name { font-size: 24px; font-weight: 700; letter-spacing: 1px; margin-bottom: 20px; }
  .contact-list { list-style: none; margin-bottom: 14px; }
  .contact-list li {
    display: flex; align-items: center; gap: 8px;
    font-size: 19px; line-height: 1.4;
  }
  .contact-list svg { width: 20px; height: 20px; flex: none; }
  .company { font-size: 19px; font-weight: 700; }
  .address { font-size: 19px; line-height: 1.25; }
</style>
</head>
<body>
<main class="canvas">
  <section class="card card--front">
    <span class="brand-mark"></span>
    <span class="brand-name brand-name--front">Heritage Hollow</span>
  </section>

  <section class="card card--back">
    <div class="back-brand">
      <span class="brand-mark brand-mark--small"></span>
      <span class="brand-name brand-name--back">Heritage<br>Hollow</span>
    </div>
    <div class="divider"></div>
    <div class="details">
      <h1 class="person-name">MAYA TORVELL</h1>
      <ul class="contact-list">
        <li>
          <svg viewBox="0 0 20 20"><rect x="1" y="1" width="18" height="18" rx="3" fill="none" stroke="#161616" stroke-width="1.6"/><path d="M6 4.5c-1 1-.5 4 2 6.8 2.6 2.8 5.5 3.6 6.5 2.6l.8-.9-2.3-2-1.2 1c-1.2-.5-3-2.3-3.5-3.6l1-1.1-1.8-2.4z" fill="#161616"/></svg>
          02 6481 7395
        </li>
        <li>
          <svg viewBox="0 0 20 20"><rect x="1.5" y="4" width="17" height="12" fill="#161616"/><path d="M1.5 4l8.5 7 8.5-7" fill="none" stroke="#fff" stroke-width="1.4"/></svg>
          maya@kelvadtrading.com.au
        </li>
        <li>
          <svg viewBox="0 0 20 20"><circle cx="10" cy="10" r="9" fill="#161616"/><g fill="none" stroke="#fff" stroke-width="1"><ellipse cx="10" cy="10" rx="4" ry="9"/><path d="M1 10h18M2.5 5.5h15M2.5 14.5h15M10 1v18"/></g></svg>
          www.heritagehollow.com.au
        </li>
      </ul>
      <p class="company">HERITAGE HOLLOW</p>
      <p class="address">PO Box Glenwarra<br>NSW 2791</p>
    </div>
  </section>
</main>
</body>
</html>
```